Personal training and nutrition business needs business card design

We need a business card that outlays our services and invites potential customers to join our team and take the first step to a healthier and more enjoyable life. We cater for any level of fitness and specialize in weight loss and conditioning, strength training, muscle gain and strength endurance. Whether you are just starting off or need some help getting to the next level of your journey we are here to get the job done.
We specialize in one on one or one on two personal training sessions and each program will be custom made to suit individual fitness goals of our clients

```html
<!DOCTYPE html>
<html lang="en">
<head>
<meta charset="utf-8">
<title>Pulse &amp; Stride – Business Card</title>
<link href="https://fonts.googleapis.com/css2?family=Raleway:wght@400;700;800&family=Lato:wght@400&family=Oswald:wght@500&display=swap" rel="stylesheet">
<style>
  :root {
    --backdrop: #a6a6a6;
    --card-dark: #202020;
    --card-light: #ffffff;
    --purple: #9a4fb3;
    --purple-soft: #a762bd;
    --ink: #111111;
    --rule: #9a9a9a;
    --white: #ffffff;
  }
  * { margin: 0; padding: 0; box-sizing: border-box; }
  html, body {
    width: 1200px; height: 1200px; overflow: hidden;
    background: var(--backdrop);
  }
  .stage {
    position: relative; width: 1200px; height: 1200px;
  }
  .card {
    position: absolute; top: 303px;
    width: 370px; height: 594px;
    text-align: center;
  }
  .card--front { left: 206px; background: var(--card-dark); }
  .card--back  { left: 606px; background: var(--card-light); border: 1px solid #e2e2e2; }

  .brand-mark {
    position: absolute; left: 50%; transform: translateX(-50%);
    width: 104px; height: 104px; border-radius: 14px;
    background: var(--purple);
  }
  .card--front .brand-mark { top: 108px; }
  .card--back  .brand-mark { top: 60px; }

  .brand-name {
    position: absolute; left: 0; right: 0;
    font-family: "Raleway", sans-serif; font-weight: 800;
    font-size: 38px; line-height: 40px; letter-spacing: 2px;
    text-transform: uppercase;
  }
  .card--front .brand-name { top: 246px; color: var(--white); }
  .card--back  .brand-name { top: 194px; color: var(--ink); }

  .tagline {
    position: absolute; left: 0; right: 0;
    font-family: "Oswald", sans-serif; font-weight: 500;
    font-size: 10.5px; letter-spacing: 1.3px;
    color: var(--purple-soft); text-transform: uppercase;
  }
  .card--front .tagline { top: 332px; }
  .card--back  .tagline { top: 279px; }

  .services {
    position: absolute; top: 462px; left: 0; right: 0;
    list-style: none;
    font-family: "Raleway", sans-serif; font-weight: 400;
    font-size: 17px; line-height: 24.7px;
    color: var(--purple-soft); text-transform: uppercase;
  }

  .person-name {
    position: absolute; top: 336px; left: 0; right: 0;
    font-family: "Raleway", sans-serif; font-weight: 700;
    font-size: 23px; color: var(--purple); text-transform: uppercase;
  }
  .person-role {
    position: absolute; top: 362px; left: 0; right: 0;
    font-family: "Lato", sans-serif; font-size: 17px; color: var(--ink);
  }
  .contact-icons {
    position: absolute; top: 395px; left: 0; right: 0;
    display: flex; justify-content: center; align-items: center; gap: 4px;
  }
  .contact-icons .rule { width: 52px; height: 1px; background: var(--rule); margin: 0 3px; }
  .icon {
    width: 25px; height: 25px; border-radius: 3px; background: var(--purple);
    display: flex; align-items: center; justify-content: center;
  }
  .contact-lines, .address {
    position: absolute; left: 0; right: 0;
    font-family: "Lato", sans-serif; font-size: 17px; line-height: 21.7px;
    color: var(--ink);
  }
  .contact-lines { top: 431px; }
  .divider {
    position: absolute; top: 506px; left: 88px; width: 195px;
    height: 1px; background: var(--rule);
  }
  .address { top: 517px; }
</style>
</head>
<body>
<main class="stage">
  <section class="card card--front">
    <div class="brand-mark"></div>
    <h1 class="brand-name">Pulse &amp;<br>Stride</h1>
    <p class="tagline">Personal training.&nbsp; Nutrition. Motivation</p>
    <ul class="services">
      <li>Weight loss &amp; conditioning</li>
      <li>Strength training</li>
      <li>Muscle gain</li>
      <li>Strength endurance</li>
    </ul>
  </section>

  <section class="card card--back">
    <div class="brand-mark"></div>
    <h2 class="brand-name">Pulse &amp;<br>Stride</h2>
    <p class="tagline">Personal training.&nbsp; Nutrition. Motivation</p>

    <p class="person-name">Daniel Reyes</p>
    <p class="person-role">Managing Director</p>

    <div class="contact-icons">
      <span class="rule"></span>
      <span class="icon" aria-label="Phone">
        <svg width="15" height="15" viewBox="0 0 16 16"><path d="M2 6c0-2 2-3 6-3s6 1 6 3v1h-3V5.5H5V7H2z M4 8h8l1 5H3z" fill="#fff"/></svg>
      </span>
      <span class="icon" aria-label="Email">
        <svg width="15" height="15" viewBox="0 0 16 16"><rect x="1.5" y="3.5" width="13" height="9" fill="none" stroke="#fff" stroke-width="1.3"/><path d="M1.5 3.5 8 9l6.5-5.5M1.5 12.5l5-4.5M14.5 12.5l-5-4.5" fill="none" stroke="#fff" stroke-width="1.1"/></svg>
      </span>
      <span class="icon" aria-label="Website">
        <svg width="15" height="15" viewBox="0 0 16 16"><circle cx="8" cy="8" r="6.3" fill="none" stroke="#fff" stroke-width="1.3"/><ellipse cx="8" cy="8" rx="2.6" ry="6.3" fill="none" stroke="#fff" stroke-width="1"/><path d="M1.7 8h12.6" stroke="#fff" stroke-width="1"/></svg>
      </span>
      <span class="rule"></span>
    </div>

    <p class="contact-lines">055-987 654 321<br>hello@pulsestride.com<br>www.pulsestride.com</p>
    <div class="divider"></div>
    <p class="address">421, Address line here<br>45452, Country Name</p>
  </section>
</main>
</body>
</html>
```